Aerospace Center needs app design

We need a design that would be a creative and innovative look of a simple idea connecting air traffic control situations with sonification.
We would like to see designs that use the elements shown in the short video which are different pads, showing 4 different colors, connecting with a degree and feeling of urgency. The different pads will be movable over screen, similar as to a whiteboard where you can move things around. Each of those pads has 4 different elements that are shown:
- ATC Event (you can chose different setups)
- Select a status (you can chose between Information, Caution and Alert. Color needs to feel more alert from Information to Alert.
- Notes box (you can open the box and write additional text on it)
- Music (you can chose different files. on the right side you can see a small group of notes. When you hover over the notes, music will be played without pressing a play or stop button.
The second video is an overview of music archival program that is connected with the pads.
Look and feel
Each slider illustrates characteristics of the customer's brand and the style your logo design should communicate.

```html
<!DOCTYPE html>
<html lang="en">
<head>
<meta charset="utf-8">
<title>Music Entries</title>
<link href="https://fonts.googleapis.com/css2?family=Poppins:wght@400;500;600;700&display=swap" rel="stylesheet">
<style>
:root{
  --brand:#7a6cff;
  --brand-soft:#a497ff;
  --ink:#363636;
  --muted:#6e6e80;
  --bg-top:#f2f3f7;
  --bg-bottom:#e8e8eb;
  --white:#ffffff;
  --green:#1fb84a;
  --red:#ff1a1a;
  --yellow:#ffcc00;
  --line:#c9c9d2;
}
*{box-sizing:border-box;margin:0;padding:0}
html,body{width:1200px;height:1196px;overflow:hidden}
body{font-family:'Poppins',sans-serif;color:var(--ink);background:var(--bg-bottom);position:relative}
.abs{position:absolute}
.c{position:absolute;transform:translateX(-50%);white-space:nowrap}
.top-area{position:absolute;left:0;top:0;width:1200px;height:461px;background:var(--bg-top)}
.app-header{position:absolute;left:0;top:0;width:1200px;height:39px;background:var(--white)}
.brand{position:absolute;display:flex;align-items:center;gap:3px;font-weight:600;color:var(--brand)}
.brand .dot{width:6px;height:6px;border-radius:50%;background:var(--brand)}
.menu-btn{left:46px;top:7px;width:25px;height:25px;border-radius:50%;background:var(--bg-top)}
.page-title{left:83px;top:11px;font-size:11.5px;font-weight:600}
.search{left:184px;top:7.5px;width:642px;height:23px;background:var(--bg-top);border-radius:2px;font-size:6px;color:#9a9aa8;padding:7px 0 0 24px}
.icon-btn{width:25px;height:25px;border-radius:50%;background:var(--bg-top)}
.avatar{left:1076px;top:7px;width:25px;height:25px;border-radius:50%;background:linear-gradient(135deg,#c79a6c,#5a3b28)}
.user-role{left:1107px;top:10px;font-size:6px;color:var(--brand)}
.user-name{left:1107px;top:18px;font-size:7px;font-weight:500}
.card{position:absolute;left:75px;width:1099px;background:var(--white);border-radius:3px}
.th{font-size:6.3px;font-weight:600;top:20px}
.row{height:47px}
.row .cell{position:absolute;top:20px;font-size:7px;color:var(--muted)}
.bar{position:absolute;left:0;top:0;width:5px;height:100%;border-radius:3px 0 0 3px}
.check{position:absolute;left:19px;top:20px;width:8px;height:8px;border:1px solid #8a8a96;border-radius:1px}
.player{position:absolute;left:750px;top:17px;width:55px;height:12px}
.notation{position:absolute;left:844px;top:6px;width:63px;height:35px;border-radius:4px;background:linear-gradient(120deg,#b9b1ff,#eeeaff)}
.sets{top:16px!important;text-align:center;line-height:10px}
.note-box{position:absolute;left:1020px;top:14px;width:71px;height:21px;border:1px solid var(--line)}
.green{color:var(--green)!important}.red{color:var(--red)!important}.yellow{color:var(--yellow)!important}
.filter-btn{position:absolute;left:42px;width:26px;height:24px;border-radius:3px}
.side-pill{position:absolute;background:var(--brand);border-radius:19px}
.section-title{position:absolute;font-size:14px;font-weight:600}
.input{position:absolute;top:12px;height:21px;border:1px solid var(--line);background:var(--white);font-size:6.5px;color:var(--muted);text-align:center;line-height:19px}
.nav-bar{position:absolute;top:694px;height:446px;background:var(--brand)}
.nav-label{position:absolute;font-size:8px;font-weight:500;color:var(--white)}
.tooltip{position:absolute;left:243px;top:786px;width:62px;height:19px;background:var(--brand-soft);color:var(--white);font-size:6.5px;font-weight:500;line-height:19px;text-align:center}
.tooltip::before{content:"";position:absolute;left:-4px;top:5.5px;border:4px solid transparent;border-left:0;border-right-color:var(--brand-soft)}
.spec{position:absolute;font-size:17px;font-weight:600}
.swatch{position:absolute;left:534px;width:37px;height:37px;border-radius:50%}
.watermark{position:absolute;left:680px;top:962px;font-size:232px;font-weight:600;line-height:1;color:#dedee2;letter-spacing:6px}
svg.ic{position:absolute;width:17px;height:17px;fill:none;stroke:var(--white);stroke-width:1.5;stroke-linecap:round;stroke-linejoin:round}
</style>
</head>
<body>
<svg width="0" height="0" style="position:absolute">
  <defs>
    <g id="i-music"><path d="M4 16a2 2 0 1 1 0-.1V5l8-2v10"/><circle cx="10" cy="13" r="2"/><path d="M4 8l8-2"/></g>
    <g id="i-sliders"><path d="M4 2v16M10 2v16M16 2v16"/><circle cx="4" cy="12" r="2"/><circle cx="10" cy="6" r="2"/><circle cx="16" cy="13" r="2"/></g>
    <g id="i-event"><circle cx="6" cy="8" r="2"/><circle cx="14" cy="8" r="2"/><path d="M2 18v-4a4 4 0 0 1 8 0v4M10 18v-4a4 4 0 0 1 8 0v4M10 2l1 2 2 .3-1.5 1.4.4 2L10 6.8 8.1 7.7l.4-2L7 4.3 9 4z"/></g>
    <g id="i-chat"><path d="M6 4h12v9h-3l-3 3v-3H6z"/><path d="M4 8H2v8h2v3l3-3h3"/><path d="M9 7h6M9 10h6"/></g>
    <g id="i-logout"><path d="M12 6V3H4v14l6 2V5L4 3"/><path d="M14 10h6M17 7l3 3-3 3"/></g>
  </defs>
</svg>

<div class="top-area"></div>

<header class="app-header">
  <div class="brand" style="left:13px;top:14px;font-size:8px"><span class="dot"></span>ARC</div>
  <div class="abs menu-btn">
    <svg width="25" height="25" viewBox="0 0 25 25"><path d="M8 9h9M8 12.5h9M8 16h9" stroke="#7a6cff" stroke-width="1.2" stroke-linecap="round"/></svg>
  </div>
  <div class="abs page-title">Music Entries</div>
  <div class="abs search">Type your text here..
    <svg class="abs" style="left:10px;top:8px" width="8" height="8" viewBox="0 0 8 8"><circle cx="3.4" cy="3.4" r="2.6" fill="none" stroke="#363636" stroke-width="1"/><path d="M5.4 5.4 7.5 7.5" stroke="#363636" stroke-width="1"/></svg>
  </div>
  <div class="abs icon-btn" style="left:1009px;top:7px">
    <svg width="25" height="25" viewBox="0 0 25 25"><rect x="8" y="9" width="10" height="7" rx="1.5" fill="none" stroke="#363636" stroke-width="1"/><path d="M8.5 10l4.5 3 4.5-3" fill="none" stroke="#363636" stroke-width="1"/></svg>
  </div>
  <div class="abs icon-btn" style="left:1041px;top:7px">
    <svg width="25" height="25" viewBox="0 0 25 25"><path d="M9 16h8l-1-2v-3a3 3 0 0 0-6 0v3z" fill="none" stroke="#363636" stroke-width="1"/><path d="M12 17.5h2" stroke="#363636" stroke-width="1"/><circle cx="16" cy="9" r="1.8" fill="#2b6cff"/></svg>
  </div>
  <div class="abs avatar" role="img" aria-label="User profile photo"></div>
  <div class="abs user-role">Admin</div>
  <div class="abs user-name">Lena Hart</div>
  <div class="abs icon-btn" style="left:1165px;top:7px">
    <svg width="25" height="25" viewBox="0 0 25 25"><circle cx="12.5" cy="12.5" r="5" fill="none" stroke="#363636" stroke-width="1.2" stroke-dasharray="3 1.2"/><circle cx="12.5" cy="12.5" r="2" fill="none" stroke="#363636" stroke-width="1"/></svg>
  </div>
</header>

<!-- Main table -->
<div class="filter-btn" style="top:76px;background:var(--white)">
  <svg width="26" height="24" viewBox="0 0 26 24"><path d="M8.5 7h9l-3.5 4.5v5l-2-1v-4z" fill="#7a6cff"/></svg>
</div>

<div class="side-pill" style="left:7px;top:118px;width:35px;height:209px">
  <svg class="ic" style="left:8px;top:28px" viewBox="0 0 20 20"><use href="#i-music"/></svg>
  <svg class="ic" style="left:8px;top:61px" viewBox="0 0 20 20"><use href="#i-sliders"/></svg>
  <svg class="ic" style="left:8px;top:95px" viewBox="0 0 20 20"><use href="#i-event"/></svg>
  <svg class="ic" style="left:8px;top:128px" viewBox="0 0 20 20"><use href="#i-chat"/></svg>
  <svg class="ic" style="left:8px;top:161px" viewBox="0 0 20 20"><use href="#i-logout"/></svg>
</div>
<svg class="abs" style="left:38px;top:154px" width="6" height="8"><path d="M5 0v8L0 4z" fill="#7a6cff"/></svg>

<div class="card" style="top:65px;height:45px">
  <div class="c th" style="left:23px">GET</div>
  <div class="c th" style="left:47px">ID</div>
  <div class="c th" style="left:87px">DATE</div>
  <div class="c th" style="left:150px">NAME</div>
  <div class="c th" style="left:250px">ORCHESTRATION REGISTER</div>
  <div class="c th" style="left:334px">TEMPO</div>
  <div class="c th" style="left:398px">DYNAMIC</div>
  <div class="c th" style="left:473px">COMPLEXITY</div>
  <div class="c th" style="left:543px">KEY</div>
  <div class="c th" style="left:610px">ATC EVENT</div>
  <div class="c th" style="left:694px">PRIORITY</div>
  <div class="c th" style="left:780px">SOUND FILE</div>
  <div class="c th" style="left:871px">NOTATION</div>
  <div class="c th" style="left:962px">SETS</div>
  <div class="c th" style="left:1052px">NOTES</div>
</div>

<svg width="0" height="0" style="position:absolute">
  <defs>
    <g id="player">
      <rect width="55" height="12" rx="6" fill="#7a6cff"/>
      <path d="M6 4v4l3.5-2z" fill="#fff"/>
      <path d="M12 6h30" stroke="#fff" stroke-width="1.2"/>
      <circle cx="16" cy="6" r="2" fill="#fff"/>
      <path d="M45 5h1.5l2-1.5v5L46.5 7H45z" fill="#fff"/>
      <path d="M50 4.5a2 2 0 0 1 0 3" stroke="#fff" stroke-width=".8" fill="none"/>
    </g>
  </defs>
</svg>

<div class="card row" style="top:120px">
  <span class="bar" style="background:var(--green)"></span><span class="check"></span>
  <span class="cell" style="left:44px">01</span><span class="cell" style="left:72px">01-02-2021</span>
  <span class="cell green" style="left:130px">Aria Tocatta</span>
  <span class="cell c" style="left:227px">Piano</span><span class="cell c" style="left:275px">Deep</span>
  <span class="cell c" style="left:334px">150</span><span class="cell c" style="left:394px">mf</span>
  <span class="cell c" style="left:470px">1</span><span class="cell c" style="left:542px">c</span>
  <span class="cell c green" style="left:609px">Landing</span><span class="cell c" style="left:694px">0</span>
  <svg class="player" viewBox="0 0 55 12"><use href="#player"/></svg>
  <div class="notation" role="img" aria-label="Sheet music notation sketch"></div>
  <span class="cell c sets" style="left:963px">Famous Classical<br>Motifs</span>
  <span class="note-box"></span>
</div>

<div class="card row" style="top:178px">
  <span class="bar" style="background:var(--red)"></span><span class="check"></span>
  <span class="cell" style="left:44px">02</span><span class="cell" style="left:72px">01-02-2021</span>
  <span class="cell red" style="left:130px">Aria Tocatta</span>
  <span class="cell c" style="left:227px">Piano</span><span class="cell c" style="left:275px">Deep</span>
  <span class="cell c" style="left:334px">150</span><span class="cell c" style="left:394px">mf</span>
  <span class="cell c" style="left:470px">1</span><span class="cell c" style="left:542px">c</span>
  <span class="cell c red" style="left:601px">Alert</span><span class="cell c" style="left:694px">0</span>
  <svg class="player" viewBox="0 0 55 12"><use href="#player"/></svg>
  <div class="notation" role="img" aria-label="Sheet music notation sketch"></div>
  <span class="cell c sets" style="left:963px">Famous Classical<br>Motifs</span>
  <span class="note-box"></span>
</div>

<div class="card row" style="top:236px">
  <span class="bar" style="background:var(--yellow)"></span><span class="check"></span>
  <span class="cell" style="left:44px">03</span><span class="cell" style="left:72px">01-02-2021</span>
  <span class="cell yellow" style="left:130px">Aria Tocatta</span>
  <span class="cell c" style="left:227px">Piano</span><span class="cell c" style="left:275px">Deep</span>
  <span class="cell c" style="left:334px">150</span><span class="cell c" style="left:394px">mf</span>
  <span class="cell c" style="left:470px">1</span><span class="cell c" style="left:542px">c</span>
  <span class="cell c yellow" style="left:601px">Alert</span><span class="cell c" style="left:694px">0</span>
  <svg class="player" viewBox="0 0 55 12"><use href="#player"/></svg>
  <div class="notation" role="img" aria-label="Sheet music notation sketch"></div>
  <span class="cell c sets" style="left:963px">Famous Classical<br>Motifs</span>
  <span class="note-box"></span>
</div>

<div class="card row" style="top:293px">
  <span class="check"></span>
  <span class="cell" style="left:44px">04</span><span class="cell" style="left:72px">01-02-2021</span>
  <span class="cell" style="left:130px">Aria Tocatta</span>
  <span class="cell c" style="left:227px">Piano</span><span class="cell c" style="left:275px">Deep</span>
  <span class="cell c" style="left:334px">150</span><span class="cell c" style="left:394px">mf</span>
  <span class="cell c" style="left:470px">1</span><span class="cell c" style="left:542px">c</span>
  <span class="cell c" style="left:601px">Alert</span><span class="cell c" style="left:694px">0</span>
  <svg class="player" viewBox="0 0 55 12"><use href="#player"/></svg>
  <div class="notation" role="img" aria-label="Sheet music notation sketch"></div>
  <span class="cell c sets" style="left:963px">Famous Classical<br>Motifs</span>
  <span class="note-box"></span>
</div>

<div class="card row" style="top:351px">
  <span class="check"></span>
  <span class="cell" style="left:44px">05</span><span class="cell" style="left:72px">01-02-2021</span>
  <span class="cell" style="left:130px">Aria Tocatta</span>
  <span class="cell c" style="left:227px">Piano</span><span class="cell c" style="left:275px">Deep</span>
  <span class="cell c" style="left:334px">150</span><span class="cell c" style="left:394px">mf</span>
  <span class="cell c" style="left:470px">1</span><span class="cell c" style="left:542px">c</span>
  <span class="cell c" style="left:601px">Alert</span><span class="cell c" style="left:694px">0</span>
  <svg class="player" viewBox="0 0 55 12"><use href="#player"/></svg>
  <div class="notation" role="img" aria-label="Sheet music notation sketch"></div>
  <span class="cell c sets" style="left:963px">Famous Classical<br>Motifs</span>
  <span class="note-box"></span>
</div>

<!-- Filter explanation -->
<div class="section-title" style="left:84px;top:483px">How Filter Works</div>
<div class="filter-btn" style="top:522px;background:var(--brand)">
  <svg width="26" height="24" viewBox="0 0 26 24"><path d="M8.5 7h9l-3.5 4.5v5l-2-1v-4z" fill="#fff"/></svg>
</div>
<div class="card" style="top:512px;height:45px">
  <div class="c th" style="left:23px">GET</div>
  <div class="c th" style="left:47px">ID</div>
  <div class="c th" style="left:87px">DATE</div>
  <div class="c th" style="left:148px">NAME</div>
  <div class="c th" style="left:250px">ORCHESTRATION REGISTER</div>
  <div class="c th" style="left:334px">TEMPO</div>
  <div class="c th" style="left:398px">DYNAMIC</div>
  <div class="c th" style="left:473px">COMPLEXITY</div>
  <div class="c th" style="left:543px">KEY</div>
  <div class="c th" style="left:618px">ATC EVENT</div>
  <div class="c th" style="left:694px">PRIORITY</div>
  <div class="c th" style="left:780px">SOUND FILE</div>
  <div class="c th" style="left:871px">NOTATION</div>
  <div class="c th" style="left:962px">SETS</div>
  <div class="c th" style="left:1051px">NOTES</div>
</div>
<div class="card" style="top:558px;height:43px;background:#f7f7f9">
  <div class="input" style="left:122px;width:61px">Aria Tocatta</div>
  <div class="input" style="left:199px;width:50px">Piano</div>
  <div class="input" style="left:256px;width:49px">Deep</div>
  <div class="input" style="left:321px;width:33px">150</div>
  <div class="input" style="left:378px;width:45px">mf</div>
  <div class="input" style="left:451px;width:48px">5</div>
  <div class="input" style="left:530px;width:30px">c</div>
  <div class="input" style="left:583px;width:70px">Landing</div>
  <div class="input" style="left:681px;width:30px">0</div>
  <div class="input" style="left:1019px;width:70px">Dummy text</div>
</div>

<!-- Menu states -->
<div class="section-title" style="left:82px;top:647px">Menu Hover Functions</div>

<div class="side-pill" style="left:111px;top:764px;width:38px;height:204px">
  <svg class="ic" style="left:10px;top:23px" viewBox="0 0 20 20"><use href="#i-music"/></svg>
  <svg class="ic" style="left:10px;top:63px" viewBox="0 0 20 20"><use href="#i-sliders"/></svg>
  <svg class="ic" style="left:10px;top:100px" viewBox="0 0 20 20"><use href="#i-event"/></svg>
  <svg class="ic" style="left:10px;top:136px" viewBox="0 0 20 20"><use href="#i-chat"/></svg>
  <svg class="ic" style="left:10px;top:169px" viewBox="0 0 20 20"><use href="#i-logout"/></svg>
</div>
<svg class="abs" style="left:146px;top:791px" width="5" height="8"><path d="M5 0v8L0 4z" fill="#7a6cff"/></svg>

<div class="nav-bar" style="left:208px;width:39px">
  <div class="brand" style="left:11px;top:26px;font-size:7.5px;color:var(--white)">ARC</div>
  <span class="abs" style="left:16px;top:16px;width:6px;height:6px;border-radius:50%;background:var(--white)"></span>
  <svg class="ic" style="left:10px;top:92px" viewBox="0 0 20 20"><use href="#i-music"/></svg>
  <svg class="ic" style="left:10px;top:132px" viewBox="0 0 20 20"><use href="#i-sliders"/></svg>
  <svg class="ic" style="left:10px;top:169px" viewBox="0 0 20 20"><use href="#i-event"/></svg>
  <svg class="ic" style="left:10px;top:205px" viewBox="0 0 20 20"><use href="#i-chat"/></svg>
  <svg class="ic" style="left:10px;top:409px" viewBox="0 0 20 20"><use href="#i-logout"/></svg>
</div>
<div class="tooltip">Music Entries</div>

<div class="nav-bar" style="left:324px;width:105px">
  <span class="abs" style="left:12px;top:16px;width:6px;height:6px;border-radius:50%;background:var(--white)"></span>
  <div class="brand" style="left:11px;top:26px;font-size:7.5px;color:var(--white)">ARC</div>
  <svg class="ic" style="left:10px;top:92px" viewBox="0 0 20 20"><use href="#i-music"/></svg>
  <div class="nav-label" style="left:37px;top:94px">Music Entries</div>
  <svg class="ic" style="left:10px;top:132px" viewBox="0 0 20 20"><use href="#i-sliders"/></svg>
  <div class="nav-label" style="left:37px;top:133px">Music Sets</div>
  <svg class="ic" style="left:10px;top:169px" viewBox="0 0 20 20"><use href="#i-event"/></svg>
  <div class="nav-label" style="left:37px;top:172px">ATC Events</div>
  <svg class="ic" style="left:10px;top:205px" viewBox="0 0 20 20"><use href="#i-chat"/></svg>
  <div class="nav-label" style="left:37px;top:206px">Help</div>
  <svg class="ic" style="left:10px;top:409px" viewBox="0 0 20 20"><use href="#i-logout"/></svg>
  <div class="nav-label" style="left:37px;top:410px">Logout</div>
</div>

<!-- Style spec -->
<div class="spec" style="left:534px;top:777px"><span style="color:var(--brand)">Fonts&nbsp; Used :</span> Poppins</div>
<div class="spec" style="left:534px;top:831px;color:var(--brand)">Colors used</div>
<span class="swatch" style="top:877px;background:var(--brand)"></span>
<div class="spec" style="left:587px;top:883px;color:var(--brand)"># 7a6cff</div>
<span class="swatch" style="top:930px;background:var(--ink)"></span>
<div class="spec" style="left:587px;top:936px"># 363636</div>

<div class="watermark">ARC</div>
</body>
</html>
```